Business Card Update, need to bring life to the card, two sided color

We need a new business card design, are moving and changing addresses and need a new look, we have the logos already attached but need a new style moving forward. Can incorporate the color of the logo (The Green) as well, maybe a solid back? We deal with safety products revolving around static electricity and safety lighting. Would like to keep same font in second logo as well.

Target Market(s)

Electrical Safety, Lighting

Contact Information for Business Card

Dale Fenwick
Vice President
Office: 770-555-4821
Cell: 770-555-3067
dale@tkfenwick.example
www.tkfenwick.example
4700 West Harbor Boulevard
Suite #150
Roswell, GA 30076

Font styles to use
Serif
Sans Serif

Requirements
Must have
• Since 1918
Nice to have
• Could use the 100 Year Logo for back of card, would like the back of card to be the same green as logo.
Should not have
• No black cards please.

```html
<!DOCTYPE html>
<html lang="en">
<head>
<meta charset="utf-8">
<title>T.K. Fenwick Business Card</title>
<link href="https://fonts.googleapis.com/css2?family=Arimo:wght@700&family=Roboto:ital,wght@0,400;0,500;1,400&display=swap" rel="stylesheet">
<style>
  :root {
    --green: #0f9a5a;
    --green-dark: #0b8a4f;
    --white: #ffffff;
    --paper: #e9ecea;
    --grey-text: #6f6f6f;
    --dark-text: #3d3d3d;
  }
  * { box-sizing: border-box; margin: 0; padding: 0; }
  html, body {
    width: 1200px; height: 768px; overflow: hidden;
    background: var(--paper);
    font-family: "Roboto", Arial, sans-serif;
  }
  .stage {
    position: relative; width: 1200px; height: 768px;
    display: flex; align-items: center; justify-content: center; gap: 40px;
  }
  .card {
    position: relative; width: 560px; height: 320px;
    background: var(--white); border-radius: 22px; overflow: hidden;
    box-shadow: 0 10px 28px rgba(0,0,0,.16);
  }

  /* back side */
  .card-back { background: var(--green); }
  .back-brand {
    position: absolute; left: 0; right: 0; top: 104px;
    display: flex; align-items: center; justify-content: center; gap: 16px;
  }
  .brand-dot {
    width: 58px; height: 58px; border-radius: 50%; background: var(--white); flex: none;
  }
  .wordmark { font-family: "Arimo", Arial, sans-serif; font-weight: 700; color: var(--green); line-height: 1; }
  .wordmark .wm-name { display: block; font-size: 34px; }
  .wordmark .wm-sub { display: block; font-size: 13.5px; margin-top: 3px; padding-left: 26px; }
  .card-back .wordmark { color: var(--white); }
  .since {
    position: absolute; left: 0; right: 0; top: 184px; text-align: center;
    font-size: 14px; font-weight: 500; letter-spacing: 3px; color: var(--white);
  }
  .back-web {
    position: absolute; left: 0; right: 0; bottom: 42px; text-align: center;
    font-size: 14px; letter-spacing: 6px; color: var(--white);
  }

  /* front side */
  .person { position: absolute; left: 36px; top: 20px; }
  .person-name { font-family: "Arimo", Arial, sans-serif; font-weight: 700; font-size: 25px; color: var(--green); }
  .person-title { font-style: italic; font-size: 14px; color: var(--grey-text); margin-top: -2px; }
  .front-wordmark { position: absolute; right: 30px; top: 24px; text-align: right; }
  .front-wordmark .wm-name { font-size: 27px; }
  .front-wordmark .wm-sub { font-size: 11.5px; padding-left: 0; }
  .band {
    position: absolute; left: 0; right: 0; top: 84px; height: 190px;
    background: linear-gradient(100deg, var(--green-dark), var(--green) 60%);
  }
  .contact { position: absolute; left: 36px; top: 14px; color: var(--white); font-size: 14.5px; line-height: 1.3; }
  .address { margin-bottom: 6px; }
  .contact-line { display: flex; align-items: center; gap: 10px; height: 20px; }
  .contact-line svg { width: 13px; height: 13px; flex: none; fill: var(--white); }
  .badge {
    position: absolute; right: 40px; top: 22px; width: 146px; height: 146px;
    border-radius: 50%; border: 6px solid var(--white);
  }
  .front-web { position: absolute; left: 36px; bottom: 14px; font-size: 15px; color: var(--dark-text); }
  .front-since { position: absolute; right: 30px; bottom: 15px; font-size: 13px; font-weight: 500; letter-spacing: 2px; color: var(--green); }
</style>
</head>
<body>
<main class="stage">
  <section class="card card-back" aria-label="Card back">
    <div class="back-brand">
      <span class="brand-dot"></span>
      <div class="wordmark">
        <span class="wm-name">T.K. Fenwick</span>
        <span class="wm-sub">Manufacturing Company, Inc.</span>
      </div>
    </div>
    <p class="since">SINCE 1918</p>
    <p class="back-web">www.tkfenwick.example</p>
  </section>

  <section class="card card-front" aria-label="Card front">
    <div class="person">
      <p class="person-name">Dale Fenwick</p>
      <p class="person-title">Vice President</p>
    </div>
    <div class="wordmark front-wordmark">
      <span class="wm-name">T.K. Fenwick</span>
      <span class="wm-sub">Manufacturing Company, Inc.</span>
    </div>
    <div class="band">
      <div class="contact">
        <p class="address">4700 West Harbor Boulevard<br>Suite #150<br>Roswell, GA 30076</p>
        <p class="contact-line">
          <svg viewBox="0 0 24 24"><path d="M6.6 10.8a15 15 0 0 0 6.6 6.6l2.2-2.2c.3-.3.7-.4 1-.2 1.1.4 2.3.6 3.6.6.6 0 1 .4 1 1V20c0 .6-.4 1-1 1A17 17 0 0 1 3 4c0-.6.4-1 1-1h3.5c.6 0 1 .4 1 1 0 1.3.2 2.5.6 3.6.1.3 0 .7-.2 1z"/></svg>
          770 555 4821
        </p>
        <p class="contact-line">
          <svg viewBox="0 0 24 24"><path d="M7 1h10a2 2 0 0 1 2 2v18a2 2 0 0 1-2 2H7a2 2 0 0 1-2-2V3a2 2 0 0 1 2-2zm0 3v14h10V4z"/></svg>
          770 555 3067
        </p>
        <p class="contact-line">
          <svg viewBox="0 0 24 24"><path d="M6 2h10v6H6zM3 9h18a1 1 0 0 1 1 1v8h-4v4H6v-4H2v-8a1 1 0 0 1 1-1zm5 8v3h8v-3z"/></svg>
          770 555 9150
        </p>
        <p class="contact-line">
          <svg viewBox="0 0 24 24"><path d="M2 5h20v14H2zm2 2v.5l8 5 8-5V7z"/></svg>
          dale@tkfenwick.example
        </p>
      </div>
      <div class="badge" role="img" aria-label="Company seal area"></div>
    </div>
    <p class="front-web">www.tkfenwick.example</p>
    <p class="front-since">SINCE 1918</p>
  </section>
</main>
</body>
</html>
```